High-end construction company needs a business card design

We need a modern looking business card that draws people in, is memorable and looks so good people will want to sick it on their fridges.
On the first side what is needed are:
Logo
My name - Tomasz Brelwik
Title - Managing Director
Website - www.varkelt.co.uk
Email - tomasz@varkelt.co.uk
Telephone - 020 5194 6281
Mobile - 07845139072
On the back side was is needed is a list of all the services we provide:
-Kitchen Renovations
-Bathroom Renovations
-House Renovations
-Garage Conversions
-Extensions
-Loft Conversions
-Conservatories
-Carpentry
-Tiling
-Electrical
-Plumbing & Heating
-Bricklaying
-Landscaping
-Decorating
-Plastering
We would like the colours to be the same shades as on the logo with grey or black for the words.
Target Market(s)
Anyone who needs building work done
Contact Information for Business Card
This business card is for a construction company which strives to deliver excellent service and quality.
The look and feel of the card should represent this.
Requirements
Must have
- On the first side what is needed are:
Logo
My name - Tomasz Brelwik
Title - Managing Director
Website - www.varkelt.co.uk
Email - tomasz@varkelt.co.uk
Telephone - 020 5194 6281
Mobile - 07845139072
Nice to have
- Cool looking features

```html
<!DOCTYPE html>
<html lang="en">
<head>
<meta charset="utf-8">
<title>Varkelt Construction Ltd – Business Card</title>
<link rel="stylesheet" href="https://fonts.googleapis.com/css2?family=PT+Sans:wght@400;700&display=swap">
<style>
  :root {
    --bg: #e4e4e4;
    --green-dark: #4a8a3c;
    --green-light: #72b843;
    --green-pale: #dfe9d9;
    --card-white: #f3f3f3;
    --ink: #333333;
    --white: #ffffff;
  }
  * { margin: 0; padding: 0; box-sizing: border-box; }
  html, body { width: 1200px; height: 960px; overflow: hidden; }
  body {
    background: var(--bg);
    font-family: "PT Sans", Arial, sans-serif;
    position: relative;
  }

  .card { position: absolute; overflow: hidden; }

  /* Services side */
  .card-services {
    left: 329px; top: 112px; width: 544px; height: 351px;
    background: var(--green-dark);
  }
  .services-panel { position: absolute; inset: 0; }
  .hero-art {
    position: absolute; left: 0; top: 52px; width: 310px; height: 238px;
    background: linear-gradient(135deg, var(--green-light) 0%, #9bcf7a 60%, var(--white) 100%);
    opacity: .55;
  }
  .web-band { position: absolute; left: 0; top: 293px; }
  .web-band-text {
    position: absolute; left: 47px; top: 294px;
    color: var(--white); font-size: 14.5px; letter-spacing: 1px; line-height: 24px;
  }
  .service-list {
    position: absolute; right: 29px; top: 32px;
    list-style: none; text-align: right;
    color: var(--white); font-size: 14.5px; line-height: 19.2px;
  }
  .service-list li::after {
    content: ""; display: inline-block; width: 5px; height: 5px;
    margin-left: 5px; border-radius: 50%;
    background: var(--green-dark); vertical-align: middle;
  }

  /* Contact side */
  .card-contact {
    left: 329px; top: 505px; width: 544px; height: 352px;
    background: var(--card-white);
  }
  .edge-stripe {
    position: absolute; right: 0; top: 0; width: 14px; height: 100%;
    background: var(--green-dark);
  }
  .edge-stripe-accent {
    position: absolute; right: 0; top: 83px; width: 14px; height: 44px;
    background: var(--green-light);
  }
  .brand {
    position: absolute; left: 40px; top: 108px;
    color: var(--green-light); font-weight: 700; text-transform: uppercase;
    line-height: 1;
  }
  .brand-name { display: block; font-size: 44px; letter-spacing: 1px; }
  .brand-sub { display: block; font-size: 13.5px; letter-spacing: 2.6px; margin-top: 4px; }
  .person { position: absolute; right: 42px; top: 87px; text-align: right; }
  .person-name { color: var(--green-dark); font-size: 18px; font-weight: 700; letter-spacing: .5px; }
  .person-title { color: var(--ink); font-size: 14.5px; margin-top: 1px; }
  .contact-list { position: absolute; left: 0; top: 215px; list-style: none; }
  .contact-item {
    width: 242px; height: 21px; margin-bottom: 5.5px;
    display: flex; align-items: center; padding-left: 42px;
    color: var(--white); font-size: 14.5px;
  }
  .contact-item:nth-child(odd) { background: var(--green-dark); }
  .contact-item:nth-child(even) { background: var(--green-light); }
  .contact-item svg { width: 16px; height: 16px; margin-right: 7px; flex: none; }
  .backdrop-art {
    position: absolute; left: 236px; top: 178px; width: 294px; height: 174px;
    background: linear-gradient(180deg, rgba(114,184,67,.05), rgba(114,184,67,.16));
  }
</style>
</head>
<body>

<section class="card card-services" aria-label="Services side">
  <svg class="services-panel" width="544" height="351" viewBox="0 0 544 351">
    <polygon points="231,0 544,0 544,351 328,351" fill="#72b843"/>
  </svg>
  <div class="hero-art" role="img" aria-label="Illustration of an excavator arm over a house and city buildings"></div>
  <svg class="web-band" width="270" height="26" viewBox="0 0 270 26">
    <polygon points="0,0 264,0 270,26 0,26" fill="#72b843"/>
  </svg>
  <span class="web-band-text">www.varkelt.co.uk</span>
  <ul class="service-list">
    <li>KITCHEN RENOVATIONS</li>
    <li>BATHROOM RENOVATIONS</li>
    <li>HOUSE RENOVATIONS</li>
    <li>GARAGE CONVERSIONS</li>
    <li>EXTENSIONS</li>
    <li>LOFT CONVERSIONS</li>
    <li>CONSERVATORIES</li>
    <li>CARPENTRY</li>
    <li>ELECTRICAL</li>
    <li>PLUMBING &amp; HEATING</li>
    <li>BRICKLAYING</li>
    <li>LANDSCAPING</li>
    <li>DECORATING</li>
    <li>PLASTERING</li>
    <li>TILING</li>
  </ul>
</section>

<section class="card card-contact" aria-label="Contact side">
  <div class="backdrop-art" role="img" aria-label="Faint decorative building silhouette"></div>
  <div class="edge-stripe"></div>
  <div class="edge-stripe-accent"></div>

  <h1 class="brand">
    <span class="brand-name">Varkelt</span>
    <span class="brand-sub">Construction Ltd</span>
  </h1>

  <div class="person">
    <p class="person-name">TOMASZ BRELWIK</p>
    <p class="person-title">Managing Director</p>
  </div>

  <ul class="contact-list">
    <li class="contact-item">
      <svg viewBox="0 0 16 16" aria-hidden="true"><path fill="#fff" d="M3.6 1.5l2.2 2.6-1.3 1.6c.9 2 2.7 3.8 4.8 4.8l1.6-1.3 2.6 2.2-1.2 2.3C7 13.4 2.6 9 2 3.2z"/></svg>
      020 5194 6281
    </li>
    <li class="contact-item">
      <svg viewBox="0 0 16 16" aria-hidden="true"><rect x="4" y="1" width="8" height="14" rx="1.5" fill="none" stroke="#fff" stroke-width="1.4"/><circle cx="8" cy="12.5" r=".9" fill="#fff"/></svg>
      07845139072
    </li>
    <li class="contact-item">
      <svg viewBox="0 0 16 16" aria-hidden="true"><rect x="1" y="3" width="14" height="10" fill="none" stroke="#fff" stroke-width="1.4"/><path d="M1 3l7 6 7-6M1 13l5-5M15 13l-5-5" fill="none" stroke="#fff" stroke-width="1.2"/></svg>
      tomasz@varkelt.co.uk
    </li>
    <li class="contact-item">
      <svg viewBox="0 0 16 16" aria-hidden="true"><g fill="none" stroke="#fff" stroke-width="1.2"><circle cx="8" cy="8" r="6.5"/><ellipse cx="8" cy="8" rx="3" ry="6.5"/><path d="M1.5 8h13M2.5 4.8h11M2.5 11.2h11"/></g></svg>
      www.varkelt.co.uk
    </li>
  </ul>
</section>

</body>
</html>
```